UK Online Escort Directory Requires a Redesigned Email Marketing Campaign (4 emails total)

These emails should be designed as marketing emails that will be sent out to approx 10,000 potential customers on a by monthly basis. The designs should be innovative, professional designs that are capable of capturing a readers attention in the blink of an eye.

We have posted this job as our in-house design capabilities are not able to create professional email designs, we therefore require a designer to redesign our email marketing campaign (4 emails total) to a professional level.

The content of the emails will be provided, along with the 5 emails that we are currently sending and the company logo. This should give the potential designer all that they need to redesign the campaign to a professional level.

Please see attached brief for more information on what is required from each individual email.

Target Market(s)

Escorts throughout the UK

Industry/Entity Type

Escort

Font styles to use
Serif
Sans Serif

Requirements
Must have
• Instant recognition of what's being offered.
Nice to have
• Imaginative / inspirational designs.
Should not have
• Any unnecessary wording or text.

```html
<!DOCTYPE html>
<html lang="en">
<head>
<meta charset="utf-8">
<title>Weekly Ad Report</title>
<link rel="stylesheet" href="https://fonts.googleapis.com/css2?family=Oswald:wght@400;500&family=Open+Sans:wght@300;400;600&display=swap">
<style>
  :root {
    --brand-pink: #e08a96;
    --band-rose: #d9747b;
    --tag-blue: #5b7ec6;
    --panel-grey: #efefef;
    --ink: #111111;
    --muted: #555555;
    --soft: #888888;
    --pill-yellow: #ffc20e;
    --premium: #a0306a;
    --rule: #bdbdbd;
    --white: #ffffff;
    --photo-tone: linear-gradient(160deg, #c9a27a 0%, #b07f5e 55%, #d8c2b0 100%);
  }
  * { box-sizing: border-box; margin: 0; padding: 0; }
  html, body { width: 1014px; height: 1200px; overflow: hidden; background: var(--white); }
  body { position: relative; font-family: "Open Sans", sans-serif; color: var(--ink); }

  .masthead { position: absolute; top: 0; left: 0; width: 1014px; height: 195px; background: var(--white); }
  .brand-name {
    position: absolute; left: 34px; top: 22px;
    font-family: "Open Sans", sans-serif; font-weight: 300; font-size: 92px;
    letter-spacing: -2px; color: var(--brand-pink); line-height: 1;
  }
  .brand-tagline {
    position: absolute; left: 44px; top: 136px;
    font-family: "Open Sans", sans-serif; font-weight: 600; font-size: 25px; color: var(--tag-blue);
  }

  .report { position: absolute; top: 195px; left: 0; width: 1014px; height: 905px; background: var(--panel-grey); }
  .report-band { position: absolute; top: 0; left: 0; width: 1014px; height: 110px; }
  .report-band-title {
    position: absolute; top: 10px; width: 100%; text-align: center;
    font-family: "Oswald", sans-serif; font-weight: 400; font-size: 38px; color: var(--white);
  }

  .stats {
    position: absolute; top: 85px; width: 100%; text-align: center;
    font-size: 29px; color: var(--ink); white-space: nowrap;
  }
  .stats .figure {
    font-family: "Oswald", sans-serif; font-weight: 500; font-size: 86px;
    vertical-align: -6px; margin: 0 6px; letter-spacing: -1px;
  }

  .price-pill {
    position: absolute; top: 213px; left: 318px; width: 378px; height: 89px;
    background: var(--pill-yellow); border-radius: 45px;
    display: flex; align-items: center; justify-content: center;
    font-size: 27px; color: var(--ink); white-space: nowrap;
  }
  .price-pill .amount { font-family: "Oswald", sans-serif; font-weight: 500; font-size: 56px; margin: 0 4px; }

  .listing-card { position: absolute; top: 355px; left: 39px; width: 938px; height: 350px; background: var(--white); }
  .listing-photo { position: absolute; top: 25px; left: 25px; width: 203px; height: 300px; background: var(--photo-tone); }
  .premium-tag {
    position: absolute; top: 27px; right: 26px; width: 153px; height: 47px;
    border: 2px solid var(--premium); color: var(--premium);
    font-size: 24px; display: flex; align-items: center; justify-content: center;
  }
  .listing-name { position: absolute; top: 84px; left: 254px; font-weight: 600; font-size: 31px; }
  .listing-area { position: absolute; top: 128px; left: 254px; font-size: 24px; color: var(--ink); }
  .listing-blurb {
    position: absolute; top: 180px; left: 254px; width: 640px;
    font-size: 23.5px; line-height: 40px; color: var(--muted);
  }

  .divider { position: absolute; top: 710px; left: 39px; width: 938px; height: 6px;
    border-top: 2px solid var(--rule); border-bottom: 2px solid var(--rule); }

  .action { position: absolute; top: 765px; width: 420px; text-align: center; }
  .action-left { left: 50px; }
  .action-right { left: 545px; }
  .action-button {
    display: inline-block; background: var(--ink); color: var(--white);
    font-size: 25px; height: 56px; line-height: 56px; padding: 0 30px; border-radius: 3px;
  }
  .action-url { margin-top: 24px; font-size: 25px; color: var(--ink); white-space: nowrap; }

  .footer { position: absolute; top: 1100px; left: 0; width: 1014px; height: 100px; background: var(--white);
    display: flex; align-items: center; justify-content: center; font-size: 21px; color: var(--soft); }
</style>
</head>
<body>
  <header class="masthead">
    <div class="brand-name">companionlist-uk.com</div>
    <div class="brand-tagline">The Escort Directory</div>
  </header>

  <main class="report">
    <svg class="report-band" width="1014" height="110" viewBox="0 0 1014 110" aria-hidden="true">
      <path d="M0 0 H1014 V63 H560 Q520 68 507 105 Q494 68 454 63 H0 Z" fill="var(--band-rose)"/>
    </svg>
    <div class="report-band-title">LAST WEEK THIS AD WAS</div>

    <p class="stats">viewed<span class="figure">963</span>times and produced <span class="figure">150</span> phone calls</p>

    <div class="price-pill">for just <span class="amount">£40.49</span>pm</div>

    <article class="listing-card">
      <div class="listing-photo" role="img" aria-label="Profile photo of the listed companion"></div>
      <div class="premium-tag">Premium</div>
      <h2 class="listing-name">Marisol,24</h2>
      <p class="listing-area">Pimlico, Westminster, Chelsa Escort</p>
      <p class="listing-blurb">One of our Top 20 London escorts, this very attractive, well proportioned blonde busty escort always has a smile on her face.</p>
    </article>

    <div class="divider"></div>

    <div class="action action-left">
      <span class="action-button">Take a look@</span>
      <p class="action-url">www.companionlist-uk.com/</p>
    </div>
    <div class="action action-right">
      <span class="action-button">Post an add@</span>
      <p class="action-url">www.companionlist-uk.com/post/add/</p>
    </div>
  </main>

  <footer class="footer">Copyright 2016 Companionlist-uk.com All Rights Reserved</footer>
</body>
</html>
```